real esate business card with company logo and name

we need a business card design for a real esate company

The company name is Walsh & Brand Pty Ltd, and we have our logo designed and will upload. We want classic or moden feel. Black or white background. looks more textured. Should include folowinginformations
Owen Walsh and Lucy Brand
Sales Agents & Onsite Manager
p: 07 5948 2063
F: 07 5948 2174
M:0431 857 219
3/42 Marlow Crescent, FERNLEA QLD 4213

We want this business card looks professonal. Thank you in advance.

Industry/Entity Type

Real Estate Agent

Contact Information for Business Card

Owen Walsh and Lucy Brand
Onsite Manager & Sales Agents
p: 07 5948 2063
M:0431 857 219

Font styles to use
Serif

Colors
000000
fbfbfb
333333
959595

Requirements
Must have
• company logo and name, black or white back ground

```html
<!DOCTYPE html>
<html lang="en">
<head>
<meta charset="utf-8">
<title>Walsh &amp; Brand Pty Ltd – Business Card</title>
<link href="https://fonts.googleapis.com/css2?family=Open+Sans:wght@400;600&family=Questrial&display=swap" rel="stylesheet">
<style>
  :root {
    --backdrop: #2f2f2f;
    --card-light: #fbfbfb;
    --card-dark: #4a4a4a;
    --ink: #333333;
    --ink-soft: #959595;
    --ink-mid: #555555;
    --band-dark: #7a7a7a;
    --band-light: #b5b5b5;
    --white: #ffffff;
  }
  * { margin: 0; padding: 0; box-sizing: border-box; }
  html, body {
    width: 1200px; height: 750px; overflow: hidden;
    background: var(--backdrop);
    font-family: "Open Sans", Arial, sans-serif;
  }
  .canvas { position: relative; width: 1200px; height: 750px; }

  .card {
    position: absolute; top: 228px;
    width: 461px; height: 262px;
    overflow: hidden;
  }
  .card--front { left: 124px; background: var(--card-light); color: var(--ink); }
  .card--back { left: 618px; background: var(--card-dark); }

  .brand-mark {
    position: absolute; left: 356px; top: 30px;
    width: 64px; height: 64px; background: var(--ink-soft);
  }
  .brand-name {
    position: absolute; right: 28px; top: 126px;
    font-family: "Questrial", Arial, sans-serif;
    font-size: 10.5px; letter-spacing: 0.6px;
    color: var(--ink);
  }

  .agents { position: absolute; left: 26px; top: 134px; }
  .agents__names { font-size: 16px; font-weight: 600; color: var(--ink-mid); letter-spacing: -0.2px; }
  .agents__role { font-size: 11px; color: var(--ink-soft); margin-top: 1px; }

  .divider {
    position: absolute; left: 26px; top: 173px;
    width: 407px; height: 1px; background: var(--ink-mid);
  }

  .contacts { position: absolute; left: 26px; top: 182px; list-style: none; }
  .contacts li {
    display: flex; align-items: center; gap: 6px;
    font-size: 10.5px; color: var(--ink); height: 17.5px;
  }
  .contacts svg { width: 12px; height: 12px; fill: var(--ink); }

  .address {
    position: absolute; right: 28px; top: 201px;
    text-align: right; font-size: 10.5px; line-height: 16px; color: var(--ink);
  }

  .footer-bands { position: absolute; left: 0; bottom: 0; width: 461px; height: 16px; }

  .back-lockup {
    position: absolute; left: 0; top: 0; width: 100%; height: 100%;
    display: flex; flex-direction: column; align-items: center;
  }
  .back-lockup__mark { margin-top: 72px; width: 90px; height: 90px; background: var(--white); }
  .back-lockup__name {
    margin-top: 28px;
    font-family: "Questrial", Arial, sans-serif;
    font-size: 12.5px; letter-spacing: 0.6px; color: var(--white);
  }
</style>
</head>
<body>
<main class="canvas">

  <section class="card card--front" aria-label="Business card front">
    <div class="brand-mark"></div>
    <p class="brand-name">WALSH &amp; BRAND PTY LTD.</p>

    <div class="agents">
      <h1 class="agents__names">Owen Walsh &amp; Lucy Brand</h1>
      <p class="agents__role">Sales Agents &amp; Onsite Manager</p>
    </div>

    <div class="divider"></div>

    <ul class="contacts">
      <li>
        <svg viewBox="0 0 24 24" aria-label="Phone"><path d="M6.6 10.8a15.1 15.1 0 0 0 6.6 6.6l2.2-2.2a1 1 0 0 1 1-.25 11.4 11.4 0 0 0 3.6.57 1 1 0 0 1 1 1V20a1 1 0 0 1-1 1A17 17 0 0 1 3 4a1 1 0 0 1 1-1h3.5a1 1 0 0 1 1 1c0 1.25.2 2.45.57 3.6a1 1 0 0 1-.25 1z"/></svg>
        07 5948 2063
      </li>
      <li>
        <svg viewBox="0 0 24 24" aria-label="Mobile"><path d="M7 1h10a2 2 0 0 1 2 2v18a2 2 0 0 1-2 2H7a2 2 0 0 1-2-2V3a2 2 0 0 1 2-2zm0 3v14h10V4z"/></svg>
        0431 857 219
      </li>
      <li>
        <svg viewBox="0 0 24 24" aria-label="Fax"><path d="M6 2h10v6H6zM3 9h18a1 1 0 0 1 1 1v8a1 1 0 0 1-1 1H3a1 1 0 0 1-1-1v-8a1 1 0 0 1 1-1zm3 8v4h12v-4z"/></svg>
        07 5948 2174
      </li>
    </ul>

    <p class="address">3/42 Marlow Crescent<br>FERNLEA QLD 4213</p>

    <svg class="footer-bands" viewBox="0 0 461 16" preserveAspectRatio="none" aria-hidden="true">
      <rect x="0" y="6" width="461" height="10" fill="var(--band-light)"/>
      <rect x="0" y="1" width="346" height="3" fill="var(--band-dark)"/>
      <rect x="376" y="0" width="85" height="3" fill="var(--ink-mid)"/>
      <polygon points="346,3 361,-4 376,3 361,10" fill="var(--card-light)" stroke="var(--band-dark)" stroke-width="1.5"/>
    </svg>
  </section>

  <section class="card card--back" aria-label="Business card back">
    <div class="back-lockup">
      <div class="back-lockup__mark"></div>
      <p class="back-lockup__name">WALSH &amp; BRAND PTY LTD.</p>
    </div>
  </section>

</main>
</body>
</html>
```